Need Business Card for eLearning Company

Need a business card designed for our company, CareerVantly.

CareerVantly has developed a complete 12 lesson eLearning course to teach you the skills you need to present yourself in a job interview. The course uses advanced learning techniques in the multimedia videos, plus contains quizzes and additional exercises to insure you get the course and can walk into any interview with confidence and ease, and get the job.

www.careervantly-example.com

Industry/Entity Type

Business

```html
<!DOCTYPE html>
<html lang="en">
<head>
<meta charset="utf-8">
<title>CareerVantly Business Card</title>
<link rel="stylesheet" href="https://fonts.googleapis.com/css2?family=Questrial&display=swap">
<style>
  :root {
    --backdrop: #e6e4e1;
    --card: #f2f2f2;
    --ink: #3b3b3b;
    --ink-soft: #555555;
    --plum: #8b1c6f;
    --leaf: #8cb52a;
    --brand-square: #3d3d3d;
  }
  * { margin: 0; padding: 0; box-sizing: border-box; }
  html, body {
    width: 1200px;
    height: 900px;
    overflow: hidden;
    background: var(--backdrop);
    font-family: "Questrial", "Century Gothic", sans-serif;
    color: var(--ink);
  }
  .sheet {
    width: 1200px;
    height: 900px;
    display: flex;
    flex-direction: column;
    align-items: center;
    justify-content: center;
    gap: 60px;
  }
  .card {
    width: 560px;
    height: 320px;
    background: var(--card);
    box-shadow: 0 2px 6px rgba(0,0,0,0.12);
    position: relative;
  }
  /* Front */
  .card-front {
    display: flex;
    align-items: center;
    justify-content: center;
    gap: 22px;
  }
  .brand-square {
    width: 64px;
    height: 64px;
    border-radius: 10px;
    background: var(--brand-square);
  }
  .brand-name {
    font-size: 46px;
    color: var(--ink);
    letter-spacing: 0.5px;
  }
  /* Back */
  .card-back {
    padding: 46px 44px;
  }
  .back-brand {
    display: flex;
    align-items: center;
    gap: 14px;
  }
  .back-brand .brand-square {
    width: 32px;
    height: 32px;
    border-radius: 5px;
  }
  .back-brand .brand-name {
    font-size: 30px;
  }
  .person {
    margin-top: 34px;
    display: flex;
    align-items: baseline;
    gap: 12px;
  }
  .person-name { font-size: 25px; color: var(--ink); }
  .person-role { font-size: 15px; letter-spacing: 1px; text-transform: uppercase; color: var(--ink); }
  .contact {
    margin-top: 26px;
    list-style: none;
    font-size: 14.5px;
    line-height: 1.75;
    color: var(--ink-soft);
  }
  .contact .label { color: var(--leaf); }
  .contact .divider { color: var(--ink-soft); margin: 0 4px; }
</style>
</head>
<body>
  <main class="sheet">
    <section class="card card-front" aria-label="Business card front">
      <span class="brand-square" aria-hidden="true"></span>
      <span class="brand-name">careervantly</span>
    </section>

    <section class="card card-back" aria-label="Business card back">
      <div class="back-brand">
        <span class="brand-square" aria-hidden="true"></span>
        <span class="brand-name">careervantly</span>
      </div>
      <div class="person">
        <span class="person-name">Dana Whitfield</span>
        <span class="person-role">Principal Consultant</span>
      </div>
      <ul class="contact">
        <li><span class="label">T</span> (555) 014-2283<span class="divider">|</span><span class="label">E</span> support@careervantly-example.com</li>
        <li>420 Harbor Lane Suite 12, Fairview, WA 98000</li>
        <li>www.careervantly-example.com</li>
      </ul>
    </section>
  </main>
</body>
</html>
```